Unique Business Card Design

Unique Business Card design for our orthotic and prosthetic company. Our logo is on our website, color is light blue. Unique shape (artificial leg shaped, vertical, etc..) preferred. Logo, business name, individual name and basic demographics needed.

Industry/Entity Type

Business

Contact Information for Business Card

Logo, Industry, Phone # Logo, "Prosthetic & Orthotic Services" Place to add individual name and contact info

Colors
cee9f5

Requirements
Must have
• The icon must be there, placement of "Prosthetic & Orthotic Services" can be moved
Nice to have
• Like the mix of light blue, and a little darker blue. One design included the icons from my website which was a nice touch

```html
<!DOCTYPE html>
<html lang="en">
<head>
<meta charset="utf-8">
<title>Stridewell Inc. Business Card</title>
<link href="https://fonts.googleapis.com/css2?family=Open+Sans:ital,wght@0,400;0,600;0,700;1,400&display=swap" rel="stylesheet">
<style>
  :root {
    --brand-blue: #1560ae;
    --band-gray: #4b4b4b;
    --text-gray: #555555;
    --divider: #d4d4d4;
    --paper: #ffffff;
    --backdrop: #3d3d3d;
  }
  * { margin: 0; padding: 0; box-sizing: border-box; }
  html, body {
    width: 1105px; height: 1200px; overflow: hidden;
    background: var(--backdrop);
    font-family: "Open Sans", Arial, sans-serif;
  }
  .card {
    position: absolute;
    left: 192px;
    width: 720px; height: 412px;
    overflow: hidden;
  }
  .card--front { top: 166px; background: var(--paper); }
  .card--back { top: 622px; background: var(--brand-blue); }

  /* front: brand lockup */
  .brand {
    position: absolute; left: 41px; top: 169px;
    display: flex; align-items: center; gap: 19px;
  }
  .brand__dot {
    width: 80px; height: 80px; border-radius: 50%;
    background: var(--brand-blue); flex: none;
  }
  .brand__name {
    color: var(--brand-blue); font-weight: 600; font-size: 24px;
    line-height: 1; letter-spacing: 0.2px;
    padding-bottom: 6px; border-bottom: 1px solid var(--brand-blue);
  }
  .brand__tagline {
    color: var(--brand-blue); font-size: 12px; font-style: italic;
    margin-top: 5px; text-align: right;
  }

  .divider {
    position: absolute; left: 363px; top: 68px;
    width: 1px; height: 279px; background: var(--divider);
  }

  /* front: contact block */
  .contact { position: absolute; left: 392px; top: 78px; color: var(--text-gray); }
  .contact__name {
    color: var(--brand-blue); font-weight: 700; font-size: 25px;
    line-height: 1.1; letter-spacing: 0.3px;
  }
  .contact__title {
    color: var(--brand-blue); font-weight: 600; font-size: 16px; margin-top: 2px;
  }
  .contact__address { font-size: 19px; line-height: 27.5px; margin-top: 10px; }
  .contact__list { list-style: none; margin-top: 8px; }
  .contact__item {
    display: flex; align-items: center; gap: 10px;
    font-size: 19px; line-height: 27.5px;
  }
  .contact__icon { width: 18px; height: 18px; fill: var(--brand-blue); flex: none; }

  .band { position: absolute; left: 0; bottom: 0; width: 720px; height: 28px; }

  /* back */
  .emblem {
    position: absolute; left: 247px; top: 93px;
    width: 226px; height: 226px; border-radius: 50%;
    background: var(--paper);
    display: flex; align-items: center; justify-content: center;
    color: var(--brand-blue); font-weight: 600; font-size: 24px;
    text-align: center; line-height: 1.2;
  }
  .back__url {
    position: absolute; left: 0; right: 0; top: 343px;
    text-align: center; color: var(--paper);
    font-size: 19px; font-style: italic; letter-spacing: 4px;
  }
</style>
</head>
<body>

<section class="card card--front">
  <div class="brand">
    <span class="brand__dot"></span>
    <div>
      <div class="brand__name">STRIDEWELL INC.</div>
      <div class="brand__tagline">Prosthetic &amp; Orthotic Services</div>
    </div>
  </div>

  <div class="divider"></div>

  <div class="contact">
    <div class="contact__name">MARLA FENWICK</div>
    <div class="contact__title">CO LPO</div>
    <div class="contact__address">820 W. 14th St.<br>Riverton, NY 10990</div>
    <ul class="contact__list">
      <li class="contact__item">
        <svg class="contact__icon" viewBox="0 0 24 24"><path d="M6.6 10.8a15.1 15.1 0 0 0 6.6 6.6l2.2-2.2c.3-.3.7-.4 1-.2 1.1.4 2.3.6 3.6.6.6 0 1 .4 1 1V20c0 .6-.4 1-1 1A17 17 0 0 1 3 4c0-.6.4-1 1-1h3.5c.6 0 1 .4 1 1 0 1.3.2 2.5.6 3.6.1.3 0 .7-.2 1z"/></svg>
        555.204.1700
      </li>
      <li class="contact__item">
        <svg class="contact__icon" viewBox="0 0 24 24"><path d="M7 1h10a2 2 0 0 1 2 2v18a2 2 0 0 1-2 2H7a2 2 0 0 1-2-2V3a2 2 0 0 1 2-2zm0 3v14h10V4zm5 15.5a1.2 1.2 0 1 0 0 2.4 1.2 1.2 0 0 0 0-2.4z"/></svg>
        555.204.3919
      </li>
      <li class="contact__item">
        <svg class="contact__icon" viewBox="0 0 24 24"><path d="M6 2h10l2 2v5H6zM3 10h18a2 2 0 0 1 2 2v6h-4v4H5v-4H1v-6a2 2 0 0 1 2-2zm4 6v4h10v-4z"/></svg>
        555-0142786
      </li>
      <li class="contact__item">
        <svg class="contact__icon" viewBox="0 0 24 24"><path d="M2 5h20v14H2zm2 2v.5l8 5.5 8-5.5V7l-8 5.5z"/></svg>
        mfenwick@stridewellinc.com
      </li>
      <li class="contact__item">
        <svg class="contact__icon" viewBox="0 0 24 24"><path d="M12 2a10 10 0 1 0 0 20 10 10 0 0 0 0-20zm-1 17.9A8 8 0 0 1 4.1 10L9 15v1a2 2 0 0 0 2 2zm6.9-2.5A2 2 0 0 0 16 16h-1v-3a1 1 0 0 0-1-1H8v-2h2a1 1 0 0 0 1-1V7h2a2 2 0 0 0 2-2v-.4a8 8 0 0 1 2.9 12.8z"/></svg>
        www.stridewellinc.com
      </li>
    </ul>
  </div>

  <svg class="band" viewBox="0 0 720 28" aria-hidden="true">
    <polygon points="0,0 474,0 465,28 0,28" fill="var(--brand-blue)"/>
    <polygon points="479,2 720,2 720,28 470,28" fill="var(--band-gray)"/>
  </svg>
</section>

<section class="card card--back">
  <div class="emblem">STRIDEWELL<br>INC.</div>
  <div class="back__url">www.stridewellinc.com</div>
</section>

</body>
</html>
```